Small Business Consulting Firm Needs Letterhead

We need a letterhead for our company "Brightpath Plus". Our company does outbound calling and mailing to business owner's companies who have taken high interest loans. These loans tend to put these businesses in a big financial bind short term, and we help them find better financial options. We would like the design to match our colors of our logo. Headers and footers would look nice, but we are open. We would want it to include our address, website, phone, and email info. Our address - 2000 E. Lamar Blvd. Suite 600Website - www.safeguardtoday.comEmail - info@safeguardtoday.comPhone - 855-726-1938
Industry/Entity Type
Financial Planning
Look and feel
Each slider illustrates characteristics of the customer's brand and the style your logo design should communicate.

```html
<!DOCTYPE html>
<html lang="en">
<head>
<meta charset="utf-8">
<title>Brightpath Plus Letterhead</title>
<link href="https://fonts.googleapis.com/css2?family=Open+Sans:wght@400;600&family=Lato:wght@400;700&family=Montserrat:wght@400&display=swap" rel="stylesheet">
<style>
  :root {
    --bg: #e6e6e6;
    --paper: #ffffff;
    --ink: #3a3a3a;
    --ink-dark: #1f1f1f;
    --rule: #9a9a9a;
    --green-dark: #5c9a32;
    --green: #76bd43;
    --blue-dark: #1a5e96;
    --blue: #0a7ac8;
  }
  html, body {
    margin: 0;
    padding: 0;
    width: 1040px;
    height: 1200px;
    overflow: hidden;
    background: var(--bg);
  }
  .canvas {
    position: relative;
    width: 1040px;
    height: 1200px;
  }
  .letterhead {
    position: absolute;
    left: 69.5px;
    top: 20px;
    width: 789px;
    height: 1016px;
    background: var(--paper);
    transform: scale(1.142);
    transform-origin: top left;
    box-shadow: 0 2px 10px rgba(0,0,0,0.12);
    overflow: hidden;
    font-family: "Open Sans", sans-serif;
    color: var(--ink);
  }
  .corner { position: absolute; }
  .corner--top { right: 0; top: 0; }
  .corner--bottom { left: 0; bottom: 0; }

  .brand {
    position: absolute;
    top: 86px;
    left: 0;
    width: 789px;
    text-align: center;
    font-family: "Montserrat", sans-serif;
    color: var(--ink-dark);
  }
  .brand__mark {
    display: block;
    width: 14px;
    height: 14px;
    margin: 0 auto 8px;
    background: var(--green);
  }
  .brand__name {
    font-size: 15.5px;
    letter-spacing: 1.6px;
    line-height: 18px;
  }
  .brand__tagline {
    font-size: 7.5px;
    letter-spacing: 4px;
    line-height: 10px;
    color: var(--ink);
  }

  .letter {
    position: absolute;
    left: 74px;
    width: 638px;
    font-size: 12.3px;
  }
  .letter p { margin: 0; }
  .letter__date { top: 183px; line-height: 16px; }
  .letter__recipient { top: 214px; line-height: 15px; }
  .letter__salutation { top: 302px; line-height: 16px; }
  .letter__body {
    top: 344px;
    line-height: 23px;
    text-align: justify;
  }
  .letter__body p { margin-bottom: 23px; }
  .letter__closing { top: 690px; line-height: 16px; }
  .letter__signer { top: 754px; }
  .letter__signer-name {
    font-size: 15.5px;
    font-weight: 600;
    color: var(--ink-dark);
    line-height: 22px;
  }
  .letter__signer-title { line-height: 20px; font-size: 12.3px; }

  .footer {
    position: absolute;
    left: 78px;
    width: 633px;
    top: 948px;
    font-family: "Lato", sans-serif;
    color: var(--ink-dark);
    text-align: center;
  }
  .footer__address { font-size: 14.5px; line-height: 18px; }
  .footer__rule { height: 1px; background: var(--rule); margin: 4px 0 5px; }
  .footer__contact { font-size: 14.5px; line-height: 18px; }
  .footer__label { color: var(--blue); font-weight: 700; }
  .footer__web { color: var(--blue); }
  .footer__web-accent { color: var(--green); }
</style>
</head>
<body>
<div class="canvas">
  <div class="letterhead">
    <svg class="corner corner--top" width="214" height="214" viewBox="0 0 214 214" role="img" aria-label="Green decorative corner accent">
      <defs>
        <linearGradient id="greenFade" x1="0" y1="0" x2="1" y2="1">
          <stop offset="0" stop-color="var(--green)"/>
          <stop offset="1" stop-color="var(--green-dark)"/>
        </linearGradient>
      </defs>
      <polygon points="0,0 214,0 214,214" fill="url(#greenFade)"/>
    </svg>
    <svg class="corner corner--bottom" width="107" height="107" viewBox="0 0 107 107" role="img" aria-label="Blue decorative corner accent">
      <defs>
        <linearGradient id="blueFade" x1="0" y1="0" x2="1" y2="1">
          <stop offset="0" stop-color="var(--blue-dark)"/>
          <stop offset="1" stop-color="var(--blue)"/>
        </linearGradient>
      </defs>
      <polygon points="0,0 0,107 107,107" fill="url(#blueFade)"/>
    </svg>

    <div class="brand">
      <span class="brand__mark"></span>
      <div class="brand__name">BRIGHTPATH PLUS</div>
      <div class="brand__tagline">CONSULTING</div>
    </div>

    <div class="letter letter__date">Issuing Date: May 5, 2018</div>
    <div class="letter letter__recipient">
      Name Of Employee Mr. XYZABC<br>
      Address of Employee<br>
      Address Line 2 etc..
    </div>
    <div class="letter letter__salutation">Dear Mr.XYZABC</div>
    <div class="letter letter__body">
      <p>Lorem Ipsum has been the industry's standard dummy text ever since the 1500s, when an unknown printer took a galley of type and scrambled it to make a type specimen book. It has survived not only five centuries, but also the leap into electronic typesetting, remaining essentially unchanged. It was popularised in the 1960s with the release of Tessaret sheets containing Lorem Ipsum passages, and more recently with desktop publishing software like Orvane PageSet including versions of Lorem Ipsum.</p>
      <p>Lorem Ipsum is simply dummy text of the printing and typesetting industry. Lorem Ipsum has been the industry's standard dummy text ever since the 1500s, when an unknown printer took a galley of type and scrambled it to make a type specimen book.</p>
      <p>It has survived not only five centuries, but also the leap into electronic typesetting, remaining essentially unchanged. It was popularised in the 1960s with the release of Tessaret sheets containing Lorem IpsumIpsum passages.</p>
    </div>
    <div class="letter letter__closing">Yours Sincerely</div>
    <div class="letter letter__signer">
      <div class="letter__signer-name">Marcus Ellery</div>
      <div class="letter__signer-title">Managing Director</div>
    </div>

    <div class="footer">
      <div class="footer__address">4170 W. Corwin Ave. Suite 310</div>
      <div class="footer__rule"></div>
      <div class="footer__contact">
        <span class="footer__label">P:</span> 855-726-1938 &nbsp;|
        <span class="footer__label">E:</span> info@brightpathplus.com |
        <span class="footer__web">www.<span class="footer__web-accent">brightpathplus</span>.com</span>
      </div>
    </div>
  </div>
</div>
</body>
</html>
```